Kestrel Facilities Business Card Design

We would now like to design business cards with the new Kestrel Facilities logo

Target Market(s)

Professional

Industry/Entity Type

Professional services

Contact Information for Business Card

Employee name, title, phone number, email address, corporate office address and logo.

Font styles to use
Sans Serif

Colors
0054AA
0677BA
7BADD7
CADEEF
E8F1F8

Requirements
Must have
• My logo
Should not have
• any other pictures or images besides my logo

```html
<!DOCTYPE html>
<html lang="en">
<head>
<meta charset="utf-8">
<title>Kestrel Facilities Business Card</title>
<link href="https://fonts.googleapis.com/css2?family=Lato:wght@400;700&family=Oswald:wght@500&display=swap" rel="stylesheet">
<style>
  :root {
    --card-blue: #0a84eb;
    --brand-blue: #0677ba;
    --ink-white: #ffffff;
    --window-light: #e8f1f8;
    --window-mid: #cadeef;
    --page-bg: #eceef1;
  }
  * { margin: 0; padding: 0; box-sizing: border-box; }
  html, body {
    width: 1200px;
    height: 900px;
    overflow: hidden;
    background: var(--page-bg);
  }
  .canvas {
    position: relative;
    width: 1200px;
    height: 900px;
  }
  .business-card {
    position: absolute;
    left: 120px;
    top: 153px;
    width: 960px;
    height: 594px;
    background: var(--card-blue);
    color: var(--ink-white);
    font-family: "Lato", sans-serif;
    box-shadow: 0 12px 30px rgba(0, 40, 90, 0.18);
  }
  .contact-block {
    position: absolute;
    left: 61px;
    top: 98px;
  }
  .person-name {
    font-family: "Oswald", sans-serif;
    font-weight: 500;
    font-size: 46px;
    line-height: 1;
    letter-spacing: -0.5px;
    transform: scaleX(0.88);
    transform-origin: left;
  }
  .person-title {
    font-size: 28px;
    line-height: 1.15;
    margin-top: 1px;
  }
  .office-address {
    margin-top: 72px;
    font-size: 28px;
    line-height: 35px;
  }
  .contact-list {
    list-style: none;
    margin-top: 54px;
    font-size: 28px;
    line-height: 37px;
  }
  .contact-list li {
    display: flex;
    align-items: center;
    gap: 8px;
  }
  .contact-icon {
    width: 30px;
    height: 30px;
    flex: none;
  }
  .brand-window {
    position: absolute;
    left: 396px;
    top: 41px;
    width: 510px;
    height: 510px;
    border-radius: 50%;
    background: radial-gradient(circle at 45% 40%, var(--window-light) 0%, #e4e6ea 55%, var(--window-mid) 100%);
    display: flex;
    flex-direction: column;
    align-items: center;
    justify-content: center;
  }
  .brand-name {
    font-family: "Lato", sans-serif;
    font-weight: 700;
    color: var(--brand-blue);
    font-size: 62px;
    line-height: 1.05;
    text-align: center;
    letter-spacing: 2px;
    text-transform: uppercase;
  }
</style>
</head>
<body>
<div class="canvas">
  <section class="business-card">
    <div class="contact-block">
      <h1 class="person-name">DANIEL MERCER</h1>
      <p class="person-title">Managing Director</p>
      <p class="office-address">118 Harbour Lane, Suite 4<br>Northfield, 30871</p>
      <ul class="contact-list">
        <li>
          <svg class="contact-icon" viewBox="0 0 24 24" aria-hidden="true">
            <path fill="#fff" d="M6.6 10.8c1.4 2.8 3.8 5.1 6.6 6.6l2.2-2.2c.3-.3.7-.4 1-.2 1.1.4 2.3.6 3.6.6.6 0 1 .4 1 1V20c0 .6-.4 1-1 1C10.6 21 3 13.4 3 4c0-.6.4-1 1-1h3.5c.6 0 1 .4 1 1 0 1.3.2 2.5.6 3.6.1.3 0 .7-.2 1l-2.3 2.2z"/>
            <path fill="none" stroke="#fff" stroke-width="1.6" d="M14 3.5a7 7 0 0 1 6.5 6.5M14 7a3.5 3.5 0 0 1 3 3"/>
          </svg>
          <span>044-310 527 864</span>
        </li>
        <li>
          <svg class="contact-icon" viewBox="0 0 24 24" aria-hidden="true">
            <rect x="2" y="5" width="20" height="14" fill="#fff"/>
            <path d="M2 5l10 8 10-8M2 19l7-7M22 19l-7-7" fill="none" stroke="var(--card-blue)" stroke-width="1.4"/>
          </svg>
          <span>hello@kestrelfm.com</span>
        </li>
        <li>
          <svg class="contact-icon" viewBox="0 0 24 24" aria-hidden="true">
            <g fill="none" stroke="#fff" stroke-width="1.6">
              <circle cx="12" cy="12" r="9.5"/>
              <ellipse cx="12" cy="12" rx="4.2" ry="9.5"/>
              <path d="M2.5 12h19M4 7h16M4 17h16M12 2.5v19"/>
            </g>
          </svg>
          <span>www.kestrelfm.com</span>
        </li>
      </ul>
    </div>
    <div class="brand-window">
      <p class="brand-name">Kestrel<br>Facilities</p>
    </div>
  </section>
</div>
</body>
</html>
```